Step and Repeat Backdrop for wedding reception photo booth

Would like to have a Step and Repeat Backdrop (8 foot high by 10 foot wide) that incorporates the wedding logo (attached) and the names Helen and Gavin. Background should be white, and wedding colors are burgundy and gold. Show me creativity :-) I have included some random samples.

```html
<!DOCTYPE html>
<html lang="en">
<head>
<meta charset="utf-8">
<title>Helen &amp; Gavin — Step and Repeat Backdrop</title>
<link rel="stylesheet" href="https://fonts.googleapis.com/css2?family=Cinzel+Decorative:wght@700&family=Cinzel:wght@600&display=swap">
<style>
  :root {
    --burgundy: #8e1a2e;
    --gold: #b8944f;
    --paper: #ffffff;
    --grid-line: #dcdcdc;
    --feature-line: #d4a3ae;
  }
  * { box-sizing: border-box; margin: 0; padding: 0; }
  html, body {
    width: 1200px;
    height: 1200px;
    overflow: hidden;
    background: var(--paper);
  }
  .canvas {
    width: 1200px;
    height: 1200px;
    display: flex;
    align-items: center;
    justify-content: center;
  }
  .backdrop {
    width: 1100px;
    height: 880px;
    display: grid;
    grid-template-columns: repeat(6, minmax(0, 1fr));
    grid-template-rows: repeat(6, minmax(0, 1fr));
    border: 1px solid var(--grid-line);
    background: var(--paper);
    overflow: hidden;
  }
  .tile {
    min-width: 0;
    border: 0.5px solid var(--grid-line);
    display: flex;
    flex-direction: column;
    align-items: center;
    justify-content: center;
    text-align: center;
  }
  .names {
    font-family: "Cinzel Decorative", serif;
    font-weight: 700;
    color: var(--burgundy);
    font-size: 26px;
    line-height: 1.05;
  }
  .names span { display: block; }
  .names .amp { font-size: 20px; line-height: 1.1; }
  .monogram {
    font-family: "Cinzel", serif;
    font-weight: 600;
    color: var(--gold);
    font-size: 48px;
    line-height: 1;
    letter-spacing: -2px;
    white-space: nowrap;
  }
  .feature {
    grid-column: 2 / 6;
    grid-row: 2 / 4;
    min-width: 0;
    border: 1.5px solid var(--feature-line);
    display: flex;
    flex-direction: column;
    align-items: center;
    justify-content: center;
    gap: 34px;
  }
  .feature .monogram { font-size: 112px; letter-spacing: -5px; }
  .feature .couple {
    font-family: "Cinzel Decorative", serif;
    font-weight: 700;
    color: var(--burgundy);
    font-size: 54px;
    line-height: 1;
    white-space: nowrap;
  }
</style>
</head>
<body>
<main class="canvas">
  <section class="backdrop" aria-label="Step and repeat backdrop for Helen and Gavin">
    <div class="tile"><span class="monogram">H&amp;G</span></div>
    <div class="tile names"><span>Helen</span><span class="amp">&amp;</span><span>Gavin</span></div>
    <div class="tile"><span class="monogram">H&amp;G</span></div>
    <div class="tile names"><span>Helen</span><span class="amp">&amp;</span><span>Gavin</span></div>
    <div class="tile"><span class="monogram">H&amp;G</span></div>
    <div class="tile names"><span>Helen</span><span class="amp">&amp;</span><span>Gavin</span></div>

    <div class="tile names"><span>Helen</span><span class="amp">&amp;</span><span>Gavin</span></div>
    <div class="feature">
      <span class="monogram">H&amp;G</span>
      <h1 class="couple">Helen &amp; Gavin</h1>
    </div>
    <div class="tile"><span class="monogram">H&amp;G</span></div>

    <div class="tile"><span class="monogram">H&amp;G</span></div>
    <div class="tile names"><span>Helen</span><span class="amp">&amp;</span><span>Gavin</span></div>

    <div class="tile names"><span>Helen</span><span class="amp">&amp;</span><span>Gavin</span></div>
    <div class="tile"><span class="monogram">H&amp;G</span></div>
    <div class="tile names"><span>Helen</span><span class="amp">&amp;</span><span>Gavin</span></div>
    <div class="tile"><span class="monogram">H&amp;G</span></div>
    <div class="tile names"><span>Helen</span><span class="amp">&amp;</span><span>Gavin</span></div>
    <div class="tile"><span class="monogram">H&amp;G</span></div>

    <div class="tile"><span class="monogram">H&amp;G</span></div>
    <div class="tile names"><span>Helen</span><span class="amp">&amp;</span><span>Gavin</span></div>
    <div class="tile"><span class="monogram">H&amp;G</span></div>
    <div class="tile names"><span>Helen</span><span class="amp">&amp;</span><span>Gavin</span></div>
    <div class="tile"><span class="monogram">H&amp;G</span></div>
    <div class="tile names"><span>Helen</span><span class="amp">&amp;</span><span>Gavin</span></div>

    <div class="tile names"><span>Helen</span><span class="amp">&amp;</span><span>Gavin</span></div>
    <div class="tile"><span class="monogram">H&amp;G</span></div>
    <div class="tile names"><span>Helen</span><span class="amp">&amp;</span><span>Gavin</span></div>
    <div class="tile"><span class="monogram">H&amp;G</span></div>
    <div class="tile names"><span>Helen</span><span class="amp">&amp;</span><span>Gavin</span></div>
    <div class="tile"><span class="monogram">H&amp;G</span></div>
  </section>
</main>
</body>
</html>
```